Website for Vornelix Capital, my new firm that raises money from investors to buy, build, own an...

Vornelix Capital needs a website! We are a new company with very experienced people, who invest in, own and build hotel properties, as well as apartments and other commercial real estate. We seek investors for our projects, and we provide safe, secure returns on their investment in our projects. Our new logo is designed to exhibit strength, class and security, and would like our website to continue on this theme. Our name, Vornelix, is a word-play on a Greek word “aristeia”, which means “excellence” and “a warriors finest moment of glory in war”. If you are in business, you realize that much of it is like war, with strategy and moves and opponents and competitors, and ever-changing economic conditions and threats that make business very much like war. We like to think that we are good at business (war), and so have named our company “Vornelix”, using the founders last name and the word “aristeia” combined. Another definition of "aristeia" is "performing at the peak of one's potential after a long struggle"...again, much like business in real life! The website design should exhibit financial security, smart moves, and positive growth towards a bright future.

Target Market(s)

The target market is smart and wealthy investors, with others such as brokers, cities and government agencies, lenders, sellers, partners, etc also looking at it.

Industry/Entity Type

Investment

Number of Pages Required

5+ page

Font styles to use
Sans Serif

Colors
fec214

Requirements
Must have
• Our website should have a landing page, a "about" or bio page, a projects page and a contact us page. Our new logo uses the colors black and gold, so this should be factored in to our site. The site should be simple, yet impactful and impressive. I have actually two logos, which can be mixed and interchanged in a complimentary way, each with their own unique look.
Nice to have
• I have uploaded a couple screenshots of a website i like, and the simplicity I mention.
Should not have
• The site should not be flashy or complicated or complex or "busy"

```html
<!DOCTYPE html>
<html lang="en">
<head>
<meta charset="utf-8">
<title>Vornelix Capital</title>
<link rel="stylesheet" href="https://fonts.googleapis.com/css2?family=Montserrat:wght@500;600;700&family=Open+Sans:wght@700&family=Roboto:wght@400;500&display=swap">
<style>
:root{
  --gold:#fec214;
  --gold-deep:#f0b20e;
  --ink:#1b1b1b;
  --dark:#1f2022;
  --cream:#f8f6ef;
  --light:#f0f0f0;
  --white:#ffffff;
  --muted:#3c3c3c;
  --line:#8a8a8a;
}
*{margin:0;padding:0;box-sizing:border-box}
html,body{width:1200px;height:3005px;overflow:hidden}
body{position:relative;background:var(--white);font-family:'Roboto',sans-serif;color:var(--ink)}
.abs{position:absolute}
.center{left:0;width:1200px;text-align:center}

/* header */
.site-header{position:absolute;top:0;left:0;width:1200px;height:100px;background:var(--white);z-index:5}
.brand{position:absolute;left:100px;top:34px;display:flex;align-items:center;gap:10px;font-family:'Montserrat',sans-serif;font-weight:700;font-size:24px;letter-spacing:2px;color:var(--ink)}
.brand-mark{width:16px;height:16px;background:var(--gold)}
.nav{position:absolute;top:40px;left:0;width:1200px;font-family:'Montserrat',sans-serif;font-weight:600;font-size:15px;letter-spacing:1px;color:var(--ink)}
.nav span{position:absolute}

/* shapes */
.bands{position:absolute;top:0;left:0}

/* labels */
.kicker{font-family:'Montserrat',sans-serif;font-weight:700;font-size:19px;letter-spacing:1.5px}
.kicker::after{content:"";display:block;width:50px;height:3px;background:var(--gold);margin:8px auto 0}
.kicker.on-gold::after{background:var(--white)}

.hero-title{font-family:'Open Sans',sans-serif;font-weight:700;font-size:41px;line-height:47px;color:var(--ink)}
.btn-outline{position:absolute;left:507px;width:186px;height:52px;border:2px solid var(--ink);border-radius:26px;font-family:'Roboto',sans-serif;font-size:16px;letter-spacing:1.5px;display:flex;align-items:center;justify-content:center}
.dots{display:flex;gap:4px;justify-content:center}
.dots i{width:9px;height:9px;border-radius:50%;border:1.5px solid var(--white)}
.dots i.on{background:var(--white)}

.about-title{font-family:'Open Sans',sans-serif;font-weight:700;font-size:40px;line-height:47px;text-transform:uppercase}
.body-copy{font-size:15.5px;line-height:23px;color:var(--muted)}

.feature{position:absolute;width:240px;text-align:center;top:1672px}
.feature .ring{width:148px;height:148px;margin:0 auto;border:2px solid #55575a;border-radius:50%;display:flex;align-items:center;justify-content:center}
.feature h3{margin-top:20px;font-family:'Roboto',sans-serif;font-weight:500;font-size:21px;color:var(--white);letter-spacing:.5px}

.contact-item{position:absolute;width:300px;text-align:center;top:2296px;font-size:19px;line-height:24px;color:var(--ink)}
.contact-item .dot{width:34px;height:34px;margin:0 auto 12px;border:2px solid var(--gold);border-radius:50%;display:flex;align-items:center;justify-content:center}
.field{position:absolute;border:1.5px solid #6a6a6a;background:transparent;font-size:15px;color:#555;padding:10px 18px}
.btn-solid{position:absolute;left:518px;top:2676px;width:166px;height:54px;border-radius:27px;background:var(--gold);color:var(--white);font-family:'Roboto',sans-serif;font-weight:500;font-size:15px;display:flex;align-items:center;justify-content:center;letter-spacing:.5px}

.footer-name{font-family:'Montserrat',sans-serif;font-weight:500;font-size:25px;letter-spacing:2px;color:var(--white)}
.footer-copy{font-size:12px;color:var(--white)}
</style>
</head>
<body>

<svg class="bands" width="1200" height="3005" viewBox="0 0 1200 3005">
  <defs>
    <linearGradient id="heroTone" x1="0" y1="0" x2="1" y2="1">
      <stop offset="0" stop-color="#fdbf16"/>
      <stop offset="1" stop-color="#f2b012"/>
    </linearGradient>
    <linearGradient id="towerTone" x1="0" y1="0" x2="0" y2="1">
      <stop offset="0" stop-color="#26272a"/>
      <stop offset="1" stop-color="#18191b"/>
    </linearGradient>
  </defs>
  <rect x="0" y="720" width="1200" height="700" fill="var(--cream)"/>
  <rect x="0" y="2050" width="1200" height="860" fill="var(--light)"/>
  <polygon points="0,100 1200,100 1200,722 0,820" fill="url(#heroTone)" role="img" aria-label="City skyline photograph washed in gold"/>
  <polygon points="0,1362 1200,1410 1200,2105 0,2055" fill="url(#towerTone)" role="img" aria-label="Photograph of glass office towers looking up, darkened"/>
  <polygon points="0,2897 1200,2836 1200,3005 0,3005" fill="#000"/>
</svg>

<header class="site-header">
  <div class="brand"><span class="brand-mark"></span>VORNELIX</div>
  <nav class="nav">
    <span style="left:550px">HOME</span>
    <span style="left:680px">ABOUT US</span>
    <span style="left:845px">PROJECTS</span>
    <span style="left:1002px">CONTACT US</span>
  </nav>
</header>

<!-- hero -->
<section>
  <div class="abs center kicker on-gold" style="top:254px">VORNELIX CAPITAL</div>
  <h1 class="abs center hero-title" style="top:304px">We are a new company with very experienced<br>people, who invest in, own and build hotel<br>properties, as well as apartments and other<br>commercial real estate.</h1>
  <div class="btn-outline" style="top:530px">LEARN MORE</div>
  <div class="abs center dots" style="top:701px"><i class="on"></i><i></i><i></i><i></i></div>
</section>

<!-- about -->
<section>
  <div class="abs center kicker" style="top:896px">ABOUT VORNELIX CAPITAL</div>
  <h2 class="abs center about-title" style="top:948px">Contrary to popular belief, Lorem<br>Ipsum is not simply random text</h2>
  <p class="abs center body-copy" style="top:1063px;left:215px;width:770px">Sed ut perspiciatis unde omnis iste natus error sit voluptatem accusantium doloremque laudantium, totam rem aperiam, eaque ipsa quae ab illo inventore veritatis et quasi architecto beatae vitae dicta sunt explicabo. Nemo enim ipsam voluptatem quia voluptas sit aspernatur aut odit aut fugit, sed quia consequuntur magni dolores eos qui ratione voluptatem sequi nesciunt.</p>
  <div class="btn-outline" style="top:1189px">MORE ABOUT US</div>
</section>

<!-- projects -->
<section>
  <div class="abs center kicker" style="top:1510px;color:var(--white)">VORNELIX CAPITAL PROJECTS</div>
  <p class="abs center body-copy" style="top:1566px;left:215px;width:770px;color:#e4e4e4">But I must explain to you how all this mistaken idea of denouncing pleasure and praising pain was born and I will give you a complete account of the system, and expound the actual teachings of the great explorer of the truth</p>

  <div class="feature" style="left:164px">
    <div class="ring">
      <svg width="64" height="72" viewBox="0 0 64 72" fill="none" stroke="#fff" stroke-width="4" stroke-linejoin="round" stroke-linecap="round">
        <path d="M32 4 L58 13 V34 C58 52 46 63 32 68 C18 63 6 52 6 34 V13 Z"/>
        <path d="M20 36 L29 45 L45 27"/>
      </svg>
    </div>
    <h3>SAFE</h3>
  </div>
  <div class="feature" style="left:479px">
    <div class="ring">
      <svg width="74" height="70" viewBox="0 0 74 70" fill="none" stroke="#fff" stroke-width="3" stroke-linejoin="round" stroke-linecap="round">
        <path d="M4 34 L37 6 L70 34"/>
        <path d="M13 27 V64 H61 V27"/>
        <path d="M52 19 V8 H59 V25"/>
        <rect x="29" y="42" width="16" height="22"/>
        <rect x="32" y="30" width="10" height="8"/>
        <path d="M34 30 V27 a3 3 0 0 1 6 0 V30"/>
      </svg>
    </div>
    <h3>SECURE RETURNS</h3>
  </div>
  <div class="feature" style="left:794px">
    <div class="ring">
      <svg width="74" height="74" viewBox="0 0 74 74" fill="none" stroke="#fff" stroke-width="3" stroke-linejoin="round" stroke-linecap="round">
        <path d="M4 20 H20 L30 14 H44 V24 H32"/>
        <path d="M4 30 H16"/>
        <path d="M40 30 L46 24 L52 30"/>
        <path d="M38 32 C26 42 26 68 46 68 C66 68 66 42 54 32 Z"/>
        <path d="M51 44 C49 41 41 41 41 46 C41 51 51 49 51 54 C51 59 43 59 41 56"/>
        <path d="M46 39 V61"/>
      </svg>
    </div>
    <h3>INVESTMENT</h3>
  </div>
</section>

<!-- contact -->
<section>
  <div class="abs center kicker" style="top:2190px">CONTACT US</div>
  <p class="abs center" style="top:2230px;font-size:15.5px;color:var(--muted)">Contact us the following general enquires</p>

  <div class="contact-item" style="left:101px">
    <div class="dot"><svg width="14" height="18" viewBox="0 0 14 18"><path d="M7 1 C3.5 1 1 3.6 1 7 C1 11 7 17 7 17 C7 17 13 11 13 7 C13 3.6 10.5 1 7 1 Z" fill="var(--gold)"/><circle cx="7" cy="7" r="2.3" fill="var(--light)"/></svg></div>
    4180 Harbor Lane, Suite 210<br>City Name, Country Code.
  </div>
  <div class="contact-item" style="left:450px">
    <div class="dot"><svg width="16" height="16" viewBox="0 0 16 16"><path d="M4 1 L6.5 4.5 L5 6.5 C6 8.5 7.5 10 9.5 11 L11.5 9.5 L15 12 L13 15 C7 15 1 9 1 3 Z" fill="var(--gold)"/></svg></div>
    001-555-01472
  </div>
  <div class="contact-item" style="left:796px">
    <div class="dot"><svg width="16" height="12" viewBox="0 0 16 12"><rect x="0" y="0" width="16" height="12" rx="1.5" fill="var(--gold)"/><path d="M1 1.5 L8 7 L15 1.5" fill="none" stroke="var(--light)" stroke-width="1.6"/></svg></div>
    info@vornelixcapital.com
  </div>

  <div class="field" style="left:100px;top:2452px;width:250px;height:40px">Name</div>
  <div class="field" style="left:366px;top:2452px;width:250px;height:40px">Phone No</div>
  <div class="field" style="left:630px;top:2452px;width:471px;height:40px">Email</div>
  <div class="field" style="left:100px;top:2522px;width:1001px;height:106px">Your message</div>
  <div class="btn-solid">SEND MESSAGE</div>
</section>

<!-- footer -->
<footer>
  <div class="abs center footer-name" style="top:2903px">VORNELIX CAPITAL</div>
  <div class="abs center footer-copy" style="top:2954px">Copyrights © 2018 Vornelix capital. All Rights Reserved.</div>
</footer>

</body>
</html>
```